Financial Advisor Resource Firm needs business card design

Need business card design for company in Omaha NE called Meridale Circle. We provide resources to financial advisors....workshop programs, retirement analysis, and insurance planning. I would like to see designs that use grays, greens, black, and white colors. The final design should communicate 'collaboration' and be simple yet attractive to financial planning clients. I will attached our logo and another picture of a puzzle piece coming together. I would like the incorporate the puzzle picture somehow, maybe on the back somehow, with color or just the gray scale....OR, the picture be the front of the card with 'Meridale' definition on it (see upload) and then company logo, employee name, title, address on the back (see ppt uploaded). The following disclosure needs to be included somewhere- Advisory services offered through Stonebrook Assets, LLC.
Updates

I uploaded a svg and ai file of the logo

Target Market(s)

Financial planning clients and financial advisors....so pretty diverse age range of about 40-70.

Industry/Entity Type

Financial Planning

Contact Information for Business Card

Tobias L. Fenwright, MBA
Founder/President
5287 E. Larkin Road
Suite 230
Omaha, NE 68190
Phone- (402) 555-0147
Cell- (402) 555-0183
Fax- (402) 555-0129
email- tobias@meridaleplan.example
web address- www.meridaleplan.example

Colors
1b1b1b
474747
d3d3d3
ffffff
9bcb3c
abd036

Requirements
Must have
• Must include logo provided, must be 2 sided, and must have disclosure...all of these items listed in project description

```html
<!DOCTYPE html>
<html lang="en">
<head>
<meta charset="utf-8">
<title>Meridale Circle – Business Card</title>
<link rel="stylesheet" href="https://fonts.googleapis.com/css2?family=Lato:wght@400;700;900&display=swap">
<style>
  :root {
    --ink: #1b1b1b;
    --graphite: #474747;
    --silver: #d3d3d3;
    --paper: #ffffff;
    --leaf: #9bcb3c;
    --lime: #abd036;
    --backdrop: #e9e9e9;
  }
  * { margin: 0; padding: 0; box-sizing: border-box; }
  html, body { width: 1200px; height: 900px; overflow: hidden; }
  body {
    background: var(--backdrop);
    font-family: "Lato", Arial, sans-serif;
    position: relative;
  }
  .card {
    position: absolute;
    left: 250px;
    width: 700px;
    height: 400px;
    overflow: hidden;
    box-shadow: 0 6px 18px rgba(0,0,0,0.18);
  }
  /* Back side */
  .card-back { top: 35px; background: var(--ink); }
  .card-back .photo {
    position: absolute; inset: 0;
    background:
      radial-gradient(ellipse at 62% 48%, #9a9a9a 0%, #6a6a6a 30%, transparent 65%),
      linear-gradient(160deg, #8c8c8c 0%, #5a5a5a 40%, #2e2e2e 75%, #1b1b1b 100%);
  }
  .card-back .definition {
    position: absolute; left: 0; right: 0; top: 150px;
    text-align: center; color: var(--paper);
    font-size: 21px; font-weight: 400; letter-spacing: 0.2px;
  }
  .card-back .rule {
    position: absolute; left: 110px; right: 110px; height: 1px;
    background: rgba(255,255,255,0.55);
  }
  .card-back .rule-top { top: 192px; }
  .card-back .rule-bottom { top: 300px; }
  .card-back .disclosure {
    position: absolute; left: 0; right: 0; top: 316px;
    text-align: center; color: var(--paper);
    font-size: 17px; letter-spacing: 0.6px; text-transform: uppercase;
  }
  /* Front side */
  .card-front { top: 465px; background: var(--paper); }
  .card-front .swoosh { position: absolute; inset: 0; }
  .holder { position: absolute; left: 48px; top: 44px; }
  .holder .name {
    color: var(--leaf); font-weight: 700; font-size: 24px;
    text-transform: uppercase; letter-spacing: 0.3px;
  }
  .holder .name .credential { color: var(--graphite); font-weight: 400; font-size: 18px; }
  .holder .title { color: var(--ink); font-size: 20px; margin-top: 1px; }
  .brand {
    position: absolute; right: 40px; top: 70px;
    display: flex; align-items: center; gap: 12px;
  }
  .brand .dot { width: 20px; height: 20px; border-radius: 50%; background: var(--leaf); }
  .brand .wordmark {
    color: var(--ink); font-weight: 400; font-size: 38px;
    text-transform: uppercase; letter-spacing: 1px;
  }
  .contacts {
    position: absolute; left: 90px; top: 190px;
    list-style: none; color: var(--ink); font-size: 19px; line-height: 25px;
  }
  .contacts li { display: flex; align-items: center; gap: 10px; }
  .contacts svg { width: 15px; height: 15px; fill: var(--leaf); flex: none; }
  .address {
    position: absolute; right: 30px; top: 250px;
    text-align: right; color: var(--silver); font-size: 16px; line-height: 21px;
  }
</style>
</head>
<body>

<section class="card card-back">
  <div class="photo" role="img" aria-label="Grayscale photograph of hands fitting puzzle pieces together"></div>
  <p class="definition">To come together and unite in common interest and focus</p>
  <div class="rule rule-top"></div>
  <div class="rule rule-bottom"></div>
  <p class="disclosure">Advisory services offered through Stonebrook Assets, LLC.</p>
</section>

<section class="card card-front">
  <svg class="swoosh" viewBox="0 0 700 400" preserveAspectRatio="none" aria-hidden="true">
    <path d="M0 322 C230 350 440 290 590 175 C490 272 260 362 0 344 Z" fill="var(--leaf)"/>
    <path d="M0 354 C230 374 430 302 560 206 C610 170 660 152 700 146 L700 400 L0 400 Z" fill="var(--ink)"/>
  </svg>

  <div class="holder">
    <p class="name">Tobias L. Fenwright, <span class="credential">MBA</span></p>
    <p class="title">Founder/President</p>
  </div>

  <div class="brand">
    <span class="dot"></span>
    <span class="wordmark">Meridale Circle</span>
  </div>

  <ul class="contacts">
    <li><svg viewBox="0 0 16 16"><path d="M2 5c0-2 2-3 3-3l1 3-2 1c1 2 3 4 5 5l1-2 3 1c0 1-1 3-3 3C6 13 2 9 2 5z"/></svg>(402) 555-0147</li>
    <li><svg viewBox="0 0 16 16"><path d="M4 1h8v14H4zM5.5 3v9h5V3z"/></svg>(402) 555-0183</li>
    <li><svg viewBox="0 0 16 16"><path d="M4 1h8v4H4zM1 6h14v6h-3v3H4v-3H1zM5 10v4h6v-4z"/></svg>(402) 555-0129</li>
    <li><svg viewBox="0 0 16 16"><path d="M1 3h14v10H1zM2.5 4.5 8 9l5.5-4.5z"/></svg>tobias@meridaleplan.example</li>
    <li><svg viewBox="0 0 16 16"><circle cx="8" cy="8" r="7"/></svg>www.meridaleplan.example</li>
  </ul>

  <p class="address">5287 E. Larkin Road<br>Suite 230 Omaha, NE 68190</p>
</section>

</body>
</html>
```